Zilata - Sketches from a quiet road

🎨 Design Guidelines
1. Overall Impression

Dignified, spiritual, timeless

Central focus on sand dunes with footsteps as the main motif

Mood: calm, light, spirituality, hope

2. Color Scheme

Background: warm sand tones (beige, golden, brown)

Light source (sun/beam): soft gold/white

Typography: gold or warm yellow, metallic effect preferred (gold foil in print)

Spine and back cover: darker gradient from sand tones to deep blue/black for strong readability

3. Imagery

Front cover: sand dunes with clear footsteps leading towards light/horizon

No figurative depictions of people

Optional: subtle Islamic ornaments or geometric borders as a background accent

4. Typography

Title: “Zīlāta” → large, serif font, elegant, in gold

Subtitle: “Sketches From A Quiet Road” → smaller, clean & modern, also gold/white

Author: Idrīs-Wahīd Salmūn Qāzinī → bottom of the front cover, smaller size

Spine: Title + Arabic word زيلاتة vertically placed, harmonized with the style

5. Back Cover

Short blurb/description (provided by client)

Highlighted keywords in large type: "Courage. Integrity. Faith."

ISBN + barcode at the bottom left

Background: continuation of the sand texture from the front cover (with or without footsteps)

6. Finishing Options (Print)

Gold foil stamping for the title

Matte cover with selective gloss (eg on the light or ornaments)

High-quality, sturdy cover stock

Target Market(s)

Islamic

Font styles to use
Serif

Requirements
Must have
• read the guidelines!
Nice to have
• read the guidelines!
Should not have
• read the guidelines!

```html
<!DOCTYPE html>
<html lang="en">
<head>
<meta charset="utf-8">
<title>Zīlāta – Sketches From A Quiet Road – Cover Wrap</title>
<link rel="stylesheet" href="https://fonts.googleapis.com/css2?family=Playfair+Display:wght@600;700&family=Lato:ital,wght@0,400;1,400&family=Open+Sans:wght@400&family=Tinos&family=Amiri:wght@700&display=swap">
<style>
  :root {
    --page: #ffffff;
    --night-top: #10213a;
    --night-mid: #0f1d33;
    --night-low: #0b1524;
    --spine: #0d1a2c;
    --gold-light: #fff1a8;
    --gold-mid: #d8b24a;
    --gold-deep: #7a5412;
    --gold-text: #ffe27a;
    --subtitle-dark: #5a3d12;
    --cream: #fbf6ea;
    --sky-top: #dcdad2;
    --sky-glow: #f8f1e0;
    --dune-light: #d7a45c;
    --dune-mid: #b47a38;
    --dune-dark: #6a3f19;
    --body-text: #f4f4f4;
    --placeholder: #ffffff;
  }
  * { margin: 0; padding: 0; box-sizing: border-box; }
  html, body {
    width: 1200px; height: 872px; overflow: hidden;
    background: var(--page);
  }
  .cover-wrap {
    position: absolute; left: 43px; top: 43px;
    width: 1114px; height: 786px;
  }
  .back-cover, .spine, .front-cover { position: absolute; top: 0; height: 786px; }

  .gold {
    background: linear-gradient(180deg, var(--gold-deep) 0%, var(--gold-mid) 45%, var(--gold-light) 100%);
    -webkit-background-clip: text; background-clip: text; color: transparent;
  }

  /* Back cover */
  .back-cover { left: 0; width: 523px; }
  .back-scene {
    position: absolute; inset: 0;
    background:
      radial-gradient(ellipse 90% 30% at 50% 40%, rgba(40,60,90,.35), transparent 70%),
      linear-gradient(180deg, var(--night-top) 0%, var(--night-mid) 45%, var(--night-low) 100%);
  }
  .back-title {
    position: absolute; left: 0; width: 523px; top: 151px;
    text-align: center;
    font-family: "Playfair Display", serif; font-weight: 600;
    font-size: 76px; line-height: 1;
  }
  .back-subtitle {
    position: absolute; left: 0; width: 523px; top: 243px;
    text-align: center; padding-left: 30px;
    font-family: "Lato", sans-serif; font-size: 18px; line-height: 22px;
    letter-spacing: 5.6px; color: var(--gold-text);
  }
  .keywords {
    position: absolute; left: 34px; width: 456px; top: 302px;
    font-family: "Lato", sans-serif; font-style: italic;
    font-size: 35px; line-height: 1; letter-spacing: .4px;
    color: var(--gold-text); white-space: nowrap;
  }
  .blurb {
    position: absolute; left: 34px; width: 456px; top: 351px;
    font-family: "Open Sans", sans-serif; font-size: 11.8px; line-height: 16.6px;
    color: var(--body-text); text-align: justify; text-align-last: center;
    letter-spacing: .2px; hyphens: auto;
  }
  .author-photo {
    position: absolute; left: 33px; top: 486px;
    width: 95px; height: 114px; background: var(--placeholder);
  }
  .author-note {
    position: absolute; left: 140px; width: 350px; top: 482px;
    font-family: "Open Sans", sans-serif; font-size: 11.8px; line-height: 16.6px;
    color: var(--body-text); text-align: justify; letter-spacing: .2px;
    hyphens: auto;
  }
  .isbn-block {
    position: absolute; left: 168px; top: 647px;
    width: 187px; height: 53px; background: var(--placeholder);
  }

  /* Spine */
  .spine { left: 523px; width: 67px; background: var(--spine); }
  .spine-title-wrap {
    position: absolute; left: 0; width: 67px; top: 171px; height: 117px;
  }
  .spine-title {
    position: absolute; left: 50%; top: 50%;
    transform: translate(-50%, -50%) rotate(90deg);
    font-family: "Playfair Display", serif; font-weight: 600;
    font-size: 38px; line-height: 1; white-space: nowrap;
  }
  .spine-arabic-wrap {
    position: absolute; left: 0; width: 67px; top: 512px; height: 106px;
  }
  .spine-arabic {
    position: absolute; left: 50%; top: 50%;
    transform: translate(-50%, -50%) rotate(90deg);
    font-family: "Amiri", serif; font-weight: 700;
    font-size: 44px; line-height: 1; white-space: nowrap;
    color: var(--gold-text);
  }

  /* Front cover */
  .front-cover { left: 590px; width: 524px; overflow: hidden; }
  .front-scene {
    position: absolute; inset: 0;
    background:
      radial-gradient(ellipse 30% 10% at 53% 42%, rgba(255,248,220,.95), transparent 70%),
      linear-gradient(180deg,
        var(--sky-top) 0%, var(--sky-glow) 38%, #f0e1bd 42%,
        #b98a55 46%, var(--dune-light) 55%, var(--dune-mid) 75%, var(--dune-dark) 100%);
  }
  .front-title {
    position: absolute; left: 0; width: 524px; top: 61px;
    text-align: center;
    font-family: "Playfair Display", serif; font-weight: 700;
    font-size: 138px; line-height: 1;
    filter: drop-shadow(0 1px 0 rgba(255,255,255,.8));
  }
  .front-subtitle {
    position: absolute; left: 0; width: 524px; top: 243px;
    text-align: center; padding-left: 6px;
    font-family: "Lato", sans-serif; font-size: 20px; line-height: 24px;
    letter-spacing: 5.8px; color: var(--subtitle-dark);
  }
  .front-author {
    position: absolute; left: 0; width: 524px; top: 704px;
    text-align: center;
    font-family: "Tinos", serif; font-size: 23px; line-height: 28px; letter-spacing: 1px;
    color: var(--cream);
  }
</style>
</head>
<body>
  <main class="cover-wrap">
    <section class="back-cover">
      <div class="back-scene" role="img" aria-label="Night view of desert dunes in deep blue tones"></div>
      <h2 class="back-title gold">Zīlāta</h2>
      <p class="back-subtitle">Sketches From A Quiet Road</p>
      <p class="keywords">COURAGE. INTEGRITY. FAITH</p>
      <p class="blurb">Lorem ipsum dolor sit amet, consectetur adipiscing elit, sed do eiusmod tempor incididunt ut labore et dolore magna aliqua. Quis ipsum suspendisse ultrices gravida. Risus commodo viverra maecenas accumsan lacus vel facilisis. Lorem ipsum dolor sit amet, consectetur adipiscing elit, sed do eiusmod tempor incididunt ut labore et dolore magna aliqua. Quis ipsum suspendisse ultrices gravida. Risus commodo viverra maecenas accumsan lacus vel facilised do eiusmod sis.</p>
      <div class="author-photo" role="img" aria-label="Author portrait placeholder"></div>
      <p class="author-note">Lorem ipsum dolor sit amet, consectetur adipiscing elit, sed do eiusmod tempor incididunt ut labore et dolore magna aliqua. Quis ipsum suspendisse ultrices gravida. Risus commodo viverra maecenas accumsan lacus vel facilisis. Quis ipsum suspendisse ultrices gravida. Risus commodo viverra maecenas accumsan lacus vel facilisis.</p>
      <div class="isbn-block" aria-label="ISBN area"></div>
    </section>

    <section class="spine">
      <div class="spine-title-wrap">
        <span class="spine-title gold">Zīlāta</span>
      </div>
      <div class="spine-arabic-wrap">
        <span class="spine-arabic" lang="ar" dir="rtl">زيلاتة</span>
      </div>
    </section>

    <section class="front-cover">
      <div class="front-scene" role="img" aria-label="Golden sand dunes at sunrise with a trail of footsteps leading toward the light on the horizon"></div>
      <h1 class="front-title gold">Zīlāta</h1>
      <p class="front-subtitle">Sketches From A Quiet Road</p>
      <p class="front-author">Idrīs-Wahīd Salmūn Qāzinī</p>
    </section>
  </main>
</body>
</html>
```